TalkHarbor - Language Coaching Services

Sleek, innovative, trendy design for Language Coaching business.

TalkHarbor is a new UK based company that provides Language Coaching services. We offer highly personalized on-line and face to face language courses. We also impart learning techniques workshops based on the latest neuroscience research for second-language acquisition.

Target Market(s)

See attached info

Industry/Entity Type

Consulting

Contact Information for Business Card

TalkHarbor
DaniaKV@talkharbor.co.uk
TalkHarbor.co.uk
London, UK

Font styles to use
Sans Serif

```html
<!DOCTYPE html>
<html lang="en">
<head>
<meta charset="utf-8">
<title>TalkHarbor Business Card</title>
<link href="https://fonts.googleapis.com/css2?family=Montserrat:wght@400;500;700&display=swap" rel="stylesheet">
<style>
  :root {
    --stage: #2a292a;
    --blue-light: #0aa6e0;
    --blue-deep: #06557f;
    --brand-blue: #1787c2;
    --name-blue: #136e9e;
    --silver: #d4d8db;
    --paper: #f1f1f1;
    --ink: #3a3a3a;
    --rule: #4a4a4a;
  }
  * { box-sizing: border-box; margin: 0; padding: 0; }
  html, body { width: 1200px; height: 895px; overflow: hidden; }
  body {
    background: var(--stage);
    font-family: "Montserrat", sans-serif;
    position: relative;
  }
  .card {
    position: absolute;
    left: 280px;
    width: 640px;
    height: 366px;
    border-radius: 22px;
    overflow: hidden;
    box-shadow: 0 10px 30px rgba(0,0,0,0.45);
  }
  .card-front {
    top: 48px;
    background: radial-gradient(ellipse 55% 70% at 48% 45%, var(--blue-light) 0%, #0688bd 45%, var(--blue-deep) 100%);
  }
  .card-back {
    top: 462px;
    background: linear-gradient(135deg, #fafafa 0%, var(--paper) 60%, #e6e6e6 100%);
  }
  .brand {
    position: absolute;
    display: flex;
    align-items: center;
  }
  .brand-mark {
    border-radius: 50%;
    border-style: solid;
    flex: none;
  }
  .brand-name {
    font-weight: 700;
    letter-spacing: 1px;
    text-transform: uppercase;
  }
  .card-front .brand {
    left: 0; right: 0; top: 0; bottom: 0;
    flex-direction: column;
    justify-content: center;
    gap: 18px;
  }
  .card-front .brand-mark { width: 96px; height: 96px; border-width: 9px; border-color: var(--silver); }
  .card-front .brand-name { font-size: 46px; color: var(--silver); }

  .card-back .brand {
    left: 34px; top: 110px; width: 250px;
    flex-direction: column;
    gap: 14px;
  }
  .card-back .brand-mark { width: 78px; height: 78px; border-width: 7px; border-color: var(--brand-blue); }
  .card-back .brand-name { font-size: 30px; color: var(--brand-blue); }

  .divider {
    position: absolute;
    left: 300px; top: 70px;
    width: 1.5px; height: 200px;
    background: var(--rule);
  }
  .contact {
    position: absolute;
    left: 330px; top: 78px;
    color: var(--ink);
  }
  .person-name {
    font-size: 30px;
    color: var(--name-blue);
    letter-spacing: -0.5px;
  }
  .person-name strong { font-weight: 700; }
  .person-name span { font-weight: 400; }
  .person-role { font-size: 15px; margin-top: 2px; }
  .contact-list { list-style: none; margin-top: 22px; }
  .contact-list li {
    display: flex; align-items: center; gap: 10px;
    font-size: 14.5px; line-height: 1.6;
  }
  .contact-list li.location { margin-bottom: 16px; }
  .contact-list svg { width: 14px; height: 14px; fill: var(--brand-blue); flex: none; }
</style>
</head>
<body>
  <section class="card card-front" aria-label="Card front">
    <div class="brand">
      <div class="brand-mark"></div>
      <div class="brand-name">TalkHarbor</div>
    </div>
  </section>

  <section class="card card-back" aria-label="Card back">
    <div class="brand">
      <div class="brand-mark"></div>
      <div class="brand-name">TalkHarbor</div>
    </div>
    <div class="divider"></div>
    <div class="contact">
      <h1 class="person-name"><strong>DANIA</strong> <span>KV</span></h1>
      <p class="person-role">Founder &amp; CEO</p>
      <ul class="contact-list">
        <li class="location">
          <svg viewBox="0 0 24 24"><path d="M12 2a7 7 0 0 0-7 7c0 5 7 13 7 13s7-8 7-13a7 7 0 0 0-7-7zm0 9.5A2.5 2.5 0 1 1 12 6.5a2.5 2.5 0 0 1 0 5z"/></svg>
          London, UK
        </li>
        <li>
          <svg viewBox="0 0 24 24"><path d="M6.6 10.8a15 15 0 0 0 6.6 6.6l2.2-2.2a1 1 0 0 1 1-.25 11.4 11.4 0 0 0 3.6.57 1 1 0 0 1 1 1V20a1 1 0 0 1-1 1A17 17 0 0 1 3 4a1 1 0 0 1 1-1h3.5a1 1 0 0 1 1 1c0 1.25.2 2.45.57 3.6a1 1 0 0 1-.25 1z"/></svg>
          020 7946 0321
        </li>
        <li>
          <svg viewBox="0 0 24 24"><path d="M2 5h20v14H2zm2 2v.5l8 5 8-5V7l-8 5z"/></svg>
          DaniaKV@talkharbor.co.uk
        </li>
        <li>
          <svg viewBox="0 0 24 24"><circle cx="12" cy="12" r="10"/></svg>
          www.talkharbor.co.uk
        </li>
      </ul>
    </div>
  </section>
</body>
</html>
```